Visitenkarten-Design für virtuelle Jobmesse & Jobbörse für Soldaten
Zielgruppe
Die KVL GmbH ist ein Unternehmen das zwei Hauptprodukte betreibt! Zum einen Jobbörse für Soldaten unter www.laufbahnwechsel-beispiel.de und zum anderen eine virtuelle Jobmesse für Soldaten unter www.merivon-beispiel.de , die wir zweimal im Jahr veranstalten.
Aufgabenstellung
Wir haben ja die beiden Produkte Laufbahnwechsel.de und die Merivon, für die bereits jeweils ein separtes Logo besteht! Diese finden Sie im Anhang! Beide werden doch jedoch von einem Unternehmen, der KVL GmbH betrieben! Aktuell nutzen wir eine Visitenkarte mit dem Logo von KVL und eine mit dem Logo der MERIVON. Gerade im Hinblick darauf, dass wir zukünftig auch weiter Plattformen in unser Portfolio aufnehmen, möchte ich hier unsere V-Karten flexibler gestalten!
Ziel soll es also sein, eine Visitenkarte zu gestalten, auf dem klar wird, dass der Mitarbeiter von der KVL GmbH kommt, die KVL GmbH aber unterschiedliche Produkte betreibt.
Im Anhang finden Sie:
1. Das Logo von KVL
2. Das Logo von Merivon
3. Die aktuelle V-Karte von KVL
4. Die aktuelle V-Karte von MERIVON
Vielleicht ein kleiner Anreiz: Aktuell nutzen wir auch zwei getrennte Geschäftspapiere. Das von www.laufbahnwechsel-beispiel.de lade ich einmal hoch! Der Designer, der auch die Visitenkarte erstellt, erhällt im Anschluss den 1:1 Auftrag in Höhe von 200 Euro für die Erstellung des Geschäftspapiers! Wenn Sie jetzt schon einen Vorschlag für das Geschäftspapier einreichen, erhöht das natürlich Ihre Chancen, wobei ich verspreche, dass wir im Falle eine Annahme das 1:1 im Anschluß dennoch starten werden!

```html
<!DOCTYPE html>
<html lang="de">
<head>
<meta charset="utf-8">
<title>Visitenkarte KVL GmbH</title>
<link href="https://fonts.googleapis.com/css2?family=Arimo:wght@400;700&display=swap" rel="stylesheet">
<style>
  :root {
    --bg: #2b2b2d;
    --card: #ffffff;
    --blue: #2d4a8a;
    --green: #4a6630;
    --grey: #7a7a7a;
    --text: #3a3a3a;
  }
  * { margin: 0; padding: 0; box-sizing: border-box; }
  html, body { width: 1200px; height: 801px; overflow: hidden; }
  body {
    background: var(--bg);
    font-family: "Arimo", Arial, sans-serif;
    position: relative;
  }
  .card {
    position: absolute;
    top: 226px;
    width: 540px;
    height: 348px;
    background: var(--card);
    overflow: hidden;
    box-shadow: 0 10px 30px rgba(0,0,0,.45);
  }
  .card--front { left: 40px; }
  .card--back { left: 620px; }
  .rules { position: absolute; inset: 0; }

  .brand { position: absolute; display: flex; align-items: center; gap: 10px; white-space: nowrap; }
  .brand__mark { width: 18px; height: 18px; flex: none; }
  .brand__mark--square { background: var(--grey); }
  .brand__mark--circle { border-radius: 50%; background: var(--green); }
  .brand__name { font-weight: 700; font-size: 20px; letter-spacing: .3px; line-height: 1; }
  .brand__name--grey { color: var(--grey); }
  .brand__name--green { color: var(--green); }

  .front__company { position: absolute; left: 40px; top: 150px; font-weight: 700; font-size: 26px; color: #555; }
  .front__site { position: absolute; left: 66px; top: 262px; font-weight: 700; font-size: 18px; color: var(--green); }
  .front__note { position: absolute; left: 40px; top: 290px; font-weight: 700; font-size: 12px; color: #555; }

  .person { position: absolute; left: 258px; top: 40px; white-space: nowrap; }
  .person__name { font-size: 30px; color: var(--blue); line-height: 1; }
  .person__role { font-size: 15px; color: var(--grey); margin-top: 4px; }

  .address { position: absolute; left: 280px; top: 128px; font-size: 15px; color: var(--text); line-height: 1.35; }

  .contact { position: absolute; left: 280px; top: 200px; font-size: 14px; color: var(--text); line-height: 1.6; white-space: nowrap; }
  .contact__label { color: var(--blue); display: inline-block; width: 62px; }
  .contact__row--mail { font-size: 12px; }
  .contact__row--mail .contact__label { width: 24px; }

  .band { position: absolute; bottom: 22px; height: 36px; display: flex; align-items: center; color: #fff; font-weight: 700; white-space: nowrap; }
  .band--green { left: 0; width: 262px; background: var(--green); padding-left: 20px; font-size: 17px; }
  .band--blue { right: 0; width: 236px; background: var(--blue); justify-content: center; font-size: 12.5px; }
</style>
</head>
<body>

  <section class="card card--front" aria-label="Vorderseite">
    <svg class="rules" width="540" height="348" viewBox="0 0 540 348" aria-hidden="true">
      <line x1="0" y1="110" x2="32" y2="110" stroke="#2d4a8a" stroke-width="3"/>
      <line x1="0" y1="116" x2="32" y2="116" stroke="#7a7a7a" stroke-width="3"/>
      <line x1="246" y1="110" x2="272" y2="110" stroke="#2d4a8a" stroke-width="3"/>
      <line x1="246" y1="116" x2="272" y2="116" stroke="#7a7a7a" stroke-width="3"/>
      <line x1="450" y1="56" x2="540" y2="56" stroke="#2d4a8a" stroke-width="3"/>
      <line x1="450" y1="62" x2="540" y2="62" stroke="#7a7a7a" stroke-width="3"/>
    </svg>

    <div class="brand" style="left:40px; top:104px;">
      <span class="brand__mark brand__mark--square"></span>
      <span class="brand__name brand__name--grey">Laufbahnwechsel</span>
    </div>
    <div class="front__company">KVL GmbH</div>

    <div class="brand" style="left:58px; top:226px;">
      <span class="brand__mark brand__mark--circle"></span>
      <span class="brand__name brand__name--green">MERIVON</span>
    </div>
    <div class="front__site">Merivon.de</div>
    <div class="front__note">ist eine Marke der KVL GmbH</div>

    <div class="person">
      <div class="person__name">Jonas Berger</div>
      <div class="person__role">Geschäftsführer</div>
    </div>

    <div class="address">Lindenweg 14<br>80000 Musterstadt</div>

    <div class="contact">
      <div><span class="contact__label">Telefon:</span>0800 - 123 45 67</div>
      <div><span class="contact__label">Mobil:</span>0151 - 000 11 222</div>
      <div class="contact__row--mail"><span class="contact__label">E.:</span>j.berger@laufbahnwechsel-beispiel.de</div>
      <div class="contact__row--mail"><span class="contact__label">E.:</span>j.berger@merivon-beispiel.de</div>
    </div>
  </section>

  <section class="card card--back" aria-label="Rückseite">
    <svg class="rules" width="540" height="348" viewBox="0 0 540 348" aria-hidden="true">
      <line x1="0" y1="138" x2="150" y2="138" stroke="#2d4a8a" stroke-width="3"/>
      <line x1="0" y1="145" x2="150" y2="145" stroke="#7a7a7a" stroke-width="3"/>
      <line x1="392" y1="138" x2="540" y2="138" stroke="#2d4a8a" stroke-width="3"/>
      <line x1="392" y1="145" x2="540" y2="145" stroke="#7a7a7a" stroke-width="3"/>
      <g fill="#8a8a8a">
        <rect x="268" y="290" width="8" height="36"/>
        <rect x="280" y="290" width="8" height="36"/>
        <rect x="292" y="290" width="8" height="36"/>
      </g>
    </svg>

    <div class="brand" style="left:165px; top:131px;">
      <span class="brand__mark brand__mark--square"></span>
      <span class="brand__name brand__name--grey">Laufbahnwechsel</span>
    </div>

    <div class="brand" style="left:208px; top:198px;">
      <span class="brand__mark brand__mark--circle"></span>
      <span class="brand__name brand__name--green">MERIVON</span>
    </div>

    <div class="band band--green">www.merivon-beispiel.de</div>
    <div class="band band--blue">www.laufbahnwechsel-beispiel.de</div>
  </section>

</body>
</html>
```